Dorwin's Coating & Renewal Letterhead Design We want to revamp out old traditional letterhead with the new logo designs that are attached. We are working on getting all our company items from vehicles, business, cards, t-shirts, letterhead to match. This should include company colors, fonts, and flow of items that we have attached below.

Industry/Entity Type

Construction Company

Font styles to use
Sans Serif
Other font styles liked:
• Bold with outline

Colors
ec1f27
ffffff

Requirements
Must have
• Company Name: Dorwin's Coating & Renewal
• Address: 4728 SW 81st Ter Halverd cove fl 39417
• Office Number: (555) 413-2986
• Email: Dorwinrenewal@mailbrook.example
• License Number: KRT8046392
Nice to have
• Company Colors: red, white, black, and grey

```html
<!DOCTYPE html>
<html lang="en">
<head>
<meta charset="utf-8">
<title>Dorwin's Coating &amp; Renewal — Letterhead</title>
<link href="https://fonts.googleapis.com/css2?family=Arimo:ital,wght@0,400;0,700;1,400&family=Tinos:ital,wght@0,400;0,700;1,400&display=swap" rel="stylesheet">
<style>
  :root {
    --brand-red: #ec1f27;
    --ink: #1e1e1e;
    --body-grey: #7a7a7a;
    --contact-grey: #555555;
    --rule-black: #2a2a2a;
    --stage: #dcdcdc;
    --paper: #ffffff;
  }
  * { box-sizing: border-box; margin: 0; padding: 0; }
  html, body {
    width: 1200px; height: 784px; overflow: hidden;
    background: var(--stage);
  }
  .stage {
    width: 1200px; height: 784px;
    display: flex; align-items: center; justify-content: center;
  }
  .letterhead {
    position: relative;
    width: 540px; height: 764px;
    background: var(--paper);
    box-shadow: 0 2px 10px rgba(0,0,0,.18);
    overflow: hidden;
    font-family: "Arimo", Arial, sans-serif;
  }
  .brand {
    position: absolute; top: 34px; right: 40px;
    width: 200px; text-align: right;
    color: var(--brand-red);
    font-family: "Arimo", Arial, sans-serif;
    font-weight: 700; font-size: 22px; line-height: 1.05;
    text-transform: uppercase;
  }
  .header-rules { position: absolute; top: 112px; right: 0; width: 260px; }
  .rule { display: block; width: 100%; }
  .rule--red { height: 5px; background: var(--brand-red); }
  .rule--black { height: 2px; background: var(--rule-black); margin-top: 5px; margin-left: 8px; width: calc(100% - 8px); }
  .contact {
    position: absolute; top: 128px; right: 40px;
    text-align: right;
    font-family: "Tinos", "Times New Roman", serif;
    font-size: 7.5px; line-height: 11px; color: var(--contact-grey);
  }
  .contact .sep { color: var(--brand-red); padding: 0 3px; }
  .letter-body {
    position: absolute; top: 168px; left: 58px; width: 410px;
    color: var(--body-grey);
    font-size: 9.4px; line-height: 13px;
    font-style: italic;
  }
  .letter-body p { margin-bottom: 13px; text-indent: 20px; }
  .letter-body p:first-child { text-indent: 0; }
  .halftone-field {
    position: absolute; left: 0; right: 0; top: 470px; height: 260px;
  }
  .footer-rules { position: absolute; left: 0; top: 690px; width: 250px; }
  .footer-rules .rule--black { margin-left: 0; width: calc(100% - 8px); }
  .web {
    position: absolute; left: 40px; top: 724px;
    font-family: "Tinos", "Times New Roman", serif;
    font-weight: 700; font-size: 10px; color: var(--ink);
  }
</style>
</head>
<body>
<div class="stage">
  <article class="letterhead">
    <svg class="halftone-field" viewBox="0 0 540 260" preserveAspectRatio="none" role="img" aria-label="Soft grey halftone dot pattern sweeping across the lower page">
      <defs>
        <linearGradient id="fieldFade" x1="0" y1="0" x2="1" y2="0.4">
          <stop offset="0" stop-color="#e6e6e6"/>
          <stop offset="0.7" stop-color="#f1f1f1"/>
          <stop offset="1" stop-color="#ffffff" stop-opacity="0"/>
        </linearGradient>
      </defs>
      <path d="M0 30 C 160 0, 330 60, 540 150 L540 260 L0 260 Z" fill="url(#fieldFade)"/>
    </svg>

    <div class="brand">Dorwin's Coating &amp; Renewal</div>

    <div class="header-rules">
      <span class="rule rule--red"></span>
      <span class="rule rule--black"></span>
    </div>

    <address class="contact">
      (555) 413-2986<span class="sep">|</span>License: KRT8046392<br>
      Dorwinrenewal@mailbrook.example<span class="sep">|</span>www.dorwinrenewal.example<br>
      4728 SW 81st Ter Halverd cove fl 39417
    </address>

    <section class="letter-body">
      <p>Lorem Ipsum is simply dummy text of the printing and typesetting industry. Lorem Ipsum has been the industry's standard dummy text ever since the 1500s, when an unknown printer took a galley of type and scrambled it to make a type specimen book. It has survived not only five centuries, but also the leap into electronic typesetting, remaining essentially unchanged. It was popularised in the 1960s with the release of Typlaro sheets containing Lorem Ipsum passages, and more recently with desktop publishing software like Quillset Composer including versions of Lorem Ipsum.</p>
      <p>It is a long established fact that a reader will be distracted by the readable content of a page when looking at its layout. The point of using Lorem Ipsum is that it has a more-or-less normal distribution of letters, as opposed to using 'Content here, content here', making it look like readable English. Many desktop publishing packages and web page editors now use Lorem Ipsum as their default model text, and a search for 'lorem ipsum' will uncover many web sites still in their infancy. Various versions have evolved over the years, sometimes by accident, sometimes on purpose (injected humour and the like).</p>
      <p>Contrary to popular belief, Lorem Ipsum is not simply random text. It has roots in a piece of classical Latin literature from 45 BC, making it over 2000 years old. Aldo Verrant, a Latin professor at Brellmoor College in Ostvale, looked up one of the more obscure Latin words, consectetur, from a Lorem Ipsum passage, and going through the cites of the word in classical literature, discovered the undoubtable source. Lorem Ipsum comes from sections 1.10.32 and 1.10.33 of "de Finibus Bonorum et Malorum" structures, to generate Lorem Ipsum which looks reasonable. The generated Lorem Ipsum is therefore always free from repetition, injected humour, or non-characteristic words etc.</p>
    </section>

    <div class="footer-rules">
      <span class="rule rule--red"></span>
      <span class="rule rule--black"></span>
    </div>

    <div class="web">www.dorwinrenewal.example</div>
  </article>
</div>
</body>
</html>
```